New business card for a regional office of a US M&A company

We need business card for a finance company, office based in Hong Kong , our Head office is in US, our business is to Merge and acquires companies , the new office will be a regional office for the Asia Pacific region. We want to use the head office logo as attached ( but don't have to be exactly the same, can be a variation to it) as a base and then add Asia Pacific alongside the logo.
We would prefer to have be bilingual Eng + Chinese, although we don't really have Chinese company name .

Industry/Entity Type

Business

Contact Information for Business Card

Clara Jo Tsang
 

VP,
APAC M&A Operations
Orin Vantage Asia Pacific Limited
 
Unit 1407, K18
18 Tai Lok Shan Road, 
Hong Kong 
 
M: +852 6038 1742
T : +852 2836 4100
F : +852 2836 4177
VOIP: 4158
 
cjtsang@orinvantage.com

Font styles to use
Serif
Sans Serif

Colors

Designer to choose colors to be used in the design.

Requirements
Must have
• APAC Office

```html
<!DOCTYPE html>
<html lang="en">
<head>
<meta charset="utf-8">
<title>Orin Vantage – Business Card</title>
<link rel="stylesheet" href="https://fonts.googleapis.com/css2?family=Open+Sans:wght@700&family=Roboto:wght@400;500&family=Roboto+Condensed:wght@700&display=swap">
<style>
  :root {
    --backdrop: #2b2b2c;
    --front-navy: #0f2740;
    --back-charcoal: #1c1d1f;
    --accent-cyan: #1fa9d0;
    --text-light: #e6e7e8;
    --text-white: #ffffff;
  }
  * { margin: 0; padding: 0; box-sizing: border-box; }
  html, body {
    width: 1200px;
    height: 960px;
    overflow: hidden;
    background: var(--backdrop);
  }
  .canvas {
    position: relative;
    width: 1200px;
    height: 960px;
  }
  .card {
    position: absolute;
    width: 600px;
    height: 342px;
  }
  .card--front {
    left: 322px;
    top: 108px;
    background: var(--front-navy);
    text-align: center;
  }
  .brand-name {
    position: absolute;
    left: 0;
    right: 0;
    top: 290px;
    top: 178px;
    font-family: "Open Sans", sans-serif;
    font-weight: 700;
    font-size: 48px;
    line-height: 1;
    color: var(--accent-cyan);
    letter-spacing: 0.5px;
  }
  .web-address {
    position: absolute;
    left: 0;
    right: 0;
    top: 284px;
    font-family: "Roboto", sans-serif;
    font-size: 14px;
    letter-spacing: 5.5px;
    color: var(--text-light);
  }
  .card--back {
    left: 320px;
    top: 493px;
    background: var(--back-charcoal);
    font-family: "Roboto", sans-serif;
    color: var(--text-light);
  }
  .accent-band {
    position: absolute;
    right: 0;
    top: 0;
    width: 73px;
    height: 100%;
    background: var(--accent-cyan);
  }
  .band-name {
    position: absolute;
    right: 0;
    top: 88px;
    width: 73px;
    font-family: "Roboto", sans-serif;
    font-weight: 500;
    font-size: 11px;
    line-height: 14px;
    letter-spacing: 0.5px;
    color: var(--text-white);
    text-align: center;
  }
  .person-name {
    position: absolute;
    left: 35px;
    top: 24px;
    font-family: "Roboto Condensed", sans-serif;
    font-weight: 700;
    font-size: 22px;
    color: var(--accent-cyan);
    text-transform: uppercase;
  }
  .person-title {
    position: absolute;
    left: 36px;
    top: 51px;
    font-weight: 500;
    font-size: 14px;
    color: var(--text-white);
  }
  .office-address {
    position: absolute;
    left: 35px;
    top: 124px;
    font-size: 15px;
    line-height: 18.5px;
    font-style: normal;
  }
  .contact-list {
    position: absolute;
    left: 35px;
    top: 225px;
    list-style: none;
    font-size: 15px;
    line-height: 19px;
  }
  .contact-list li {
    display: flex;
    align-items: center;
    gap: 8px;
  }
  .contact-icon {
    width: 15px;
    height: 15px;
    fill: var(--accent-cyan);
  }
  .voip {
    position: absolute;
    left: 35px;
    top: 291px;
    font-size: 15px;
  }
</style>
</head>
<body>
<main class="canvas">

  <section class="card card--front" aria-label="Card front">
    <h1 class="brand-name">ORIN VANTAGE</h1>
    <p class="web-address">www.orinvantage.com</p>
  </section>

  <section class="card card--back" aria-label="Card back">
    <h2 class="person-name">Clara Jo Tsang</h2>
    <p class="person-title">VP</p>

    <address class="office-address">
      APAC M&amp;A Operations<br>
      Orin Vantage Asia Pacific Limited<br>
      Unit 1407, K18<br>
      18 Tai Lok Shan Road<br>
      Hong Kong
    </address>

    <ul class="contact-list">
      <li>
        <svg class="contact-icon" viewBox="0 0 16 16" aria-hidden="true"><path d="M3.6 1.5l2.2 2.6c.3.4.3.9 0 1.3L4.7 6.6c.8 1.9 2.8 3.9 4.7 4.7l1.2-1.1c.4-.3.9-.3 1.3 0l2.6 2.2c.4.3.4.9.1 1.3l-1.1 1.2c-.6.6-1.5.8-2.3.5C6.7 14 2 9.3.6 4.8.3 4 .5 3.1 1.1 2.5l1.2-1.1c.4-.3 1-.3 1.3.1z"/></svg>
        +852 2836 4100
      </li>
      <li>
        <svg class="contact-icon" viewBox="0 0 16 16" aria-hidden="true"><path d="M4.5 0h7c.8 0 1.5.7 1.5 1.5v13c0 .8-.7 1.5-1.5 1.5h-7C3.7 16 3 15.3 3 14.5v-13C3 .7 3.7 0 4.5 0zm.3 2v10.5h6.4V2H4.8zM8 13.3a.9.9 0 100 1.8.9.9 0 000-1.8z"/></svg>
        +852 6038 1742
      </li>
      <li>
        <svg class="contact-icon" viewBox="0 0 16 16" aria-hidden="true"><path d="M4 1h8v4H4V1zM1.5 6h13c.8 0 1.5.7 1.5 1.5V13c0 .6-.4 1-1 1H1c-.6 0-1-.4-1-1V7.5C0 6.7.7 6 1.5 6zM3 10v2h10v-2H3zm9.5-2.8a.8.8 0 100 1.6.8.8 0 000-1.6z"/></svg>
        +852 2836 4177
      </li>
    </ul>

    <p class="voip">VOIP: 4158</p>

    <div class="accent-band"></div>
    <p class="band-name">ORIN<br>VANTAGE</p>
  </section>

</main>
</body>
</html>
```